VENTURE CAPITAL GROUP BUSINESS CARD DESIGN

Venture Capital Group based in SF looking for a bold business card design. No trendy colour explosion, 3D effects etc. Just "simple" optical effects. Works on your brain, keeps your eye focused and sticks to your mind.
Target Market(s)
Technology startups
Industry/Entity Type
Venture Capital
Contact Information for Business Card
DESMOND WHITLAKE
MANAGING PARTNER
187 FENWORTH ST SAN FRANCISCO, CA 94187
415.555.0142 O
415.555.0147 F
415.555.0193 C
desmond@veldtmoorcapital.ventures

```html
<!DOCTYPE html>
<html lang="en">
<head>
<meta charset="utf-8">
<title>Veldtmoor Capital – Business Card</title>
<link rel="stylesheet" href="https://fonts.googleapis.com/css2?family=Cormorant+Garamond:wght@400;500;700&family=Cormorant+SC:wght@500&display=swap">
<style>
  :root {
    --green: #1f9a45;
    --green-light: #4cc768;
    --green-dark: #0f6a2a;
    --ink: #6b6b6b;
    --paper: #fbfbfb;
    --backdrop: #e9e9e6;
  }
  * { box-sizing: border-box; margin: 0; padding: 0; }
  html, body {
    width: 1200px; height: 1023px; overflow: hidden;
    background: var(--backdrop);
  }
  .sheet {
    position: relative; width: 1200px; height: 1023px;
    display: flex; flex-direction: column; align-items: center; justify-content: center; gap: 56px;
  }
  .card {
    position: relative; width: 700px; height: 400px;
    box-shadow: 0 8px 24px rgba(0,0,0,.12);
  }
  .card-front { background: var(--paper); }
  .card-back {
    background: radial-gradient(ellipse at 60% 55%, var(--green-light) 0%, var(--green) 45%, var(--green-dark) 100%);
  }
  .wordmark {
    position: absolute; left: 330px; top: 110px;
    display: flex; align-items: center; gap: 12px;
    font-family: "Cormorant Garamond", serif; font-weight: 700;
    font-size: 30px; letter-spacing: 2px; color: var(--green);
  }
  .wordmark-dot {
    width: 22px; height: 22px; border-radius: 50%; background: var(--green);
  }
  .holder { position: absolute; left: 46px; top: 218px; }
  .holder-name {
    font-family: "Cormorant SC", serif; font-weight: 500;
    font-size: 28px; color: var(--green); letter-spacing: .5px;
  }
  .holder-title {
    font-family: "Cormorant Garamond", serif; font-size: 15px; color: var(--ink); margin-top: 2px;
  }
  .contacts {
    position: absolute; left: 372px; top: 228px; list-style: none;
    font-family: "Cormorant Garamond", serif; font-size: 17px; color: var(--ink);
  }
  .contacts li { display: flex; align-items: center; gap: 10px; height: 29px; }
  .contacts svg { width: 20px; height: 20px; flex: none; }
  .address {
    position: absolute; left: 404px; top: 352px;
    font-family: "Cormorant Garamond", serif; font-weight: 700;
    font-size: 17px; color: var(--green);
  }
</style>
</head>
<body>
<main class="sheet">
  <section class="card card-front">
    <div class="wordmark"><span class="wordmark-dot"></span>VELDTMOOR CAPITAL</div>

    <div class="holder">
      <div class="holder-name">Desmond Whitlake</div>
      <div class="holder-title">Founder/ Owner</div>
    </div>

    <ul class="contacts">
      <li>
        <svg viewBox="0 0 20 20" aria-hidden="true"><circle cx="10" cy="10" r="10" fill="var(--green)"/><path d="M5 8c0-2 2-3 5-3s5 1 5 3l-2 1-1-1.5H8L7 9zM6 10h8l1 4H5z" fill="#fff"/></svg>
        415.555.0142
      </li>
      <li>
        <svg viewBox="0 0 20 20" aria-hidden="true"><circle cx="10" cy="10" r="10" fill="var(--green)"/><path d="M7 5h6v3H7zM5 8h10v5h-2v-2H7v2H5zM7 12h6v3H7z" fill="#fff"/></svg>
        415.555.0147
      </li>
      <li>
        <svg viewBox="0 0 20 20" aria-hidden="true"><circle cx="10" cy="10" r="10" fill="var(--green)"/><path d="M7 5c1 0 2 2 2 3s-1 1-1 2 2 3 3 3 1-1 2-1 3 1 3 2-1 2-2 2C9 16 4 11 4 7c0-1 2-2 3-2z" fill="#fff"/></svg>
        415.555.0193
      </li>
      <li>
        <svg viewBox="0 0 20 20" aria-hidden="true"><circle cx="10" cy="10" r="10" fill="var(--green)"/><rect x="5" y="6.5" width="10" height="7" fill="#fff"/><path d="M5 6.5l5 4 5-4" fill="none" stroke="var(--green)" stroke-width="1"/></svg>
        desmond@veldtmoorcapital.ventures
      </li>
    </ul>

    <div class="address">187 Fenworth St San Francisco, CA 94187</div>
  </section>

  <section class="card card-back" aria-label="Card reverse"></section>
</main>
</body>
</html>
```